Kestrel Facilities Business Card Design

We would now like to design business cards with the new Kestrel Facilities logo

Target Market(s)

Professional

Industry/Entity Type

Professional services

Contact Information for Business Card

Employee name, title, phone number, email address, corporate office address and logo.

Font styles to use
Sans Serif

Colors
0054AA
0677BA
7BADD7
CADEEF
E8F1F8

Requirements
Must have
• My logo
Should not have
• any other pictures or images besides my logo

```html
<!DOCTYPE html>
<html lang="en">
<head>
<meta charset="utf-8">
<title>Kestrel Facilities Business Card</title>
<link href="https://fonts.googleapis.com/css2?family=Figtree:wght@400;700&display=swap" rel="stylesheet">
<style>
  :root {
    --brand-blue: #3777bd;
    --accent-gray: #a3a1a2;
    --card-white: #ffffff;
    --ink: #1d1d1f;
    --backdrop: #8c8c8c;
  }
  html, body {
    margin: 0;
    padding: 0;
    width: 1160px;
    height: 1200px;
    overflow: hidden;
    background: var(--backdrop);
    font-family: "Figtree", Arial, sans-serif;
  }
  .canvas {
    position: relative;
    width: 1160px;
    height: 1200px;
  }
  .card {
    position: absolute;
    left: 199px;
    width: 778px;
    height: 441px;
    background: var(--card-white);
    overflow: hidden;
  }
  .card--front { top: 105px; }
  .card--back { top: 634px; }
  .card__bands {
    position: absolute;
    inset: 0;
  }
  .band-blue { fill: var(--brand-blue); }
  .band-gray { fill: var(--accent-gray); }

  .brand {
    position: absolute;
    display: flex;
    align-items: center;
    gap: 16px;
    color: var(--brand-blue);
    font-weight: 700;
    text-transform: uppercase;
    line-height: 1.05;
  }
  .brand__square {
    flex: none;
    background: var(--brand-blue);
  }
  .brand__name { display: block; }

  .card--front .brand {
    left: 73px;
    top: 150px;
    font-size: 44px;
    letter-spacing: 1px;
  }
  .card--front .brand__square { width: 56px; height: 56px; }

  .card--back .brand {
    left: 0;
    right: 0;
    top: 172px;
    justify-content: center;
    font-size: 50px;
    letter-spacing: 1px;
  }
  .card--back .brand__square { width: 64px; height: 64px; }

  .divider {
    position: absolute;
    left: 400px;
    top: 96px;
    width: 2px;
    height: 245px;
    background: var(--brand-blue);
  }

  .details {
    position: absolute;
    left: 449px;
    top: 92px;
    color: var(--ink);
  }
  .details__name {
    margin: 0;
    font-size: 31px;
    font-weight: 700;
    color: var(--brand-blue);
    letter-spacing: 0.2px;
    line-height: 1;
  }
  .details__title {
    margin: 6px 0 0;
    font-size: 21px;
    font-weight: 400;
  }
  .details__address {
    margin: 28px 0 0;
    font-style: normal;
    font-size: 21px;
    line-height: 28px;
  }
  .contact-list {
    list-style: none;
    margin: 24px 0 0;
    padding: 0;
    font-size: 21px;
    line-height: 29px;
  }
  .contact-list__item {
    display: flex;
    align-items: center;
    gap: 8px;
  }
  .contact-list__icon {
    width: 18px;
    height: 18px;
    flex: none;
    fill: var(--brand-blue);
  }
</style>
</head>
<body>
<main class="canvas">

  <section class="card card--front" aria-label="Business card front">
    <svg class="card__bands" viewBox="0 0 778 441" width="778" height="441" aria-hidden="true">
      <polygon class="band-blue" points="0,0 778,0 778,30 264,27 222,55 0,55"/>
      <polygon class="band-gray" points="270,35 778,38 778,52 246,50"/>
      <polygon class="band-gray" points="0,390 522,393 504,406 0,406"/>
      <polygon class="band-blue" points="0,413 511,415 554,386 778,386 778,441 0,441"/>
    </svg>

    <div class="brand">
      <span class="brand__square"></span>
      <span class="brand__name">Kestrel<br>Facilities</span>
    </div>

    <div class="divider"></div>

    <div class="details">
      <h1 class="details__name">DARA WHITCOMBE</h1>
      <p class="details__title">Co-Founder</p>
      <address class="details__address">
        4180 N. Harbor Lane<br>
        Suite 702 Larkfield 14
      </address>
      <ul class="contact-list">
        <li class="contact-list__item">
          <svg class="contact-list__icon" viewBox="0 0 24 24" aria-hidden="true"><path d="M2 9c0-3 4-5 10-5s10 2 10 5v2h-5V9H7v2H2z M5 12h14l2 8H3z"/></svg>
          +254-160-47213
        </li>
        <li class="contact-list__item">
          <svg class="contact-list__icon" viewBox="0 0 24 24" aria-hidden="true"><path d="M2 6h20v12H2z M2 6l10 7 10-7" stroke="#fff" stroke-width="1.5"/></svg>
          info@kestrelfacilities.com
        </li>
        <li class="contact-list__item">
          <svg class="contact-list__icon" viewBox="0 0 24 24" aria-hidden="true"><circle cx="12" cy="12" r="10"/><path d="M4 12h16 M12 2c-4 4-4 16 0 20 M12 2c4 4 4 16 0 20" stroke="#fff" stroke-width="1.2" fill="none"/></svg>
          www.kestrelfacilities.com
        </li>
      </ul>
    </div>
  </section>

  <section class="card card--back" aria-label="Business card back">
    <div class="brand">
      <span class="brand__square"></span>
      <span class="brand__name">Kestrel<br>Facilities</span>
    </div>
  </section>

</main>
</body>
</html>
```